Business Card Design Project - 2 sided

We need a business card design for a card having one business on each side (ie. two businesses on one card). Would like a design that incorporates logo, tagline and normal fields (name, position, address, phone).

Would also like an allowance for small font text along the bottom (text to be determined, but less than 50 characters).

NB. Attached logo for Harbor Quill has two variations - either can be used.

www.harborquill-example.com / www.velmaro-example.com

```html
<!DOCTYPE html>
<html lang="en">
<head>
<meta charset="utf-8">
<title>Harbor Quill / Velmaro – Business Card</title>
<link rel="stylesheet" href="https://fonts.googleapis.com/css2?family=Open+Sans:wght@400;600;700&family=Open+Sans+Condensed:wght@700&display=swap">
<style>
  :root {
    --backdrop: #4a2a14;
    --card: #ffffff;
    --ink: #3a3a3a;
    --ink-soft: #444444;
    --rule: #555555;
    --brand-navy: #2d2f6e;
  }
  * { box-sizing: border-box; margin: 0; padding: 0; }
  html, body { width: 1200px; height: 412px; overflow: hidden; }
  body {
    background: var(--backdrop);
    font-family: "Open Sans", Arial, sans-serif;
    color: var(--ink);
    position: relative;
  }
  .card {
    position: absolute;
    top: 64px;
    width: 497px;
    height: 284px;
    background: var(--card);
    box-shadow: 0 4px 14px rgba(0,0,0,.45);
  }
  .card--front { left: 75px; }
  .card--back { left: 629px; }

  .brand {
    position: absolute;
    left: 0; right: 0;
    text-align: center;
  }
  .card--front .brand { top: 80px; }
  .brand__name--front {
    font-size: 24px;
    font-weight: 400;
    letter-spacing: 1px;
    color: var(--brand-navy);
  }
  .card--back .brand { top: 46px; }
  .brand__name--back {
    font-size: 30px;
    font-weight: 400;
    letter-spacing: 1px;
    line-height: 1.2;
    color: var(--ink);
  }

  .tagline {
    position: absolute;
    left: 0; right: 0;
    text-align: center;
    color: #222;
  }
  .card--front .tagline { top: 114px; font-size: 11px; font-weight: 600; }
  .card--back .tagline {
    top: 88px;
    font-family: "Open Sans Condensed", "Arial Narrow", sans-serif;
    font-weight: 700;
    font-size: 14px;
    color: #333;
  }

  .contact {
    position: absolute;
    top: 153px;
    left: 0; right: 0;
    text-align: center;
    color: var(--ink-soft);
  }
  .contact__name { font-size: 16px; font-weight: 700; color: #333; line-height: 22px; }
  .contact__title { font-size: 13px; font-weight: 400; }
  .contact__row {
    display: flex;
    justify-content: center;
    gap: 6px;
    font-size: 13px;
    line-height: 21px;
  }
  .contact__item { display: inline-flex; align-items: center; gap: 2px; }
  .icon { width: 11px; height: 11px; fill: var(--ink-soft); }

  .divider {
    position: absolute;
    top: 222px;
    left: 33px; right: 34px;
    border-top: 1px solid var(--rule);
  }
  .address {
    position: absolute;
    top: 230px;
    left: 0; right: 0;
    text-align: center;
    font-size: 13px;
    color: var(--ink-soft);
  }
  .fineprint {
    position: absolute;
    top: 252px;
    left: 0; right: 0;
    text-align: center;
    font-size: 11.8px;
    color: var(--ink-soft);
  }
</style>
</head>
<body>
<svg width="0" height="0" style="position:absolute" aria-hidden="true">
  <defs>
    <symbol id="i-phone" viewBox="0 0 12 12"><path d="M3 1l2 2-1 1.5c.6 1.4 1.6 2.4 3 3L8.5 6.5l2 2L9 10.5C5 10 2 7 1.5 3z"/></symbol>
    <symbol id="i-mobile" viewBox="0 0 12 12"><path d="M3.5 0h5a1 1 0 0 1 1 1v10a1 1 0 0 1-1 1h-5a1 1 0 0 1-1-1V1a1 1 0 0 1 1-1zm.5 2v6h4V2z"/></symbol>
    <symbol id="i-fax" viewBox="0 0 12 12"><path d="M3 1h6v3H3zM1 5h10v6H1zm2 2v1h2V7zm4 0v1h2V7z"/></symbol>
    <symbol id="i-mail" viewBox="0 0 12 12"><path d="M1 4l5-3 5 3v7H1zm1.5 1L6 7.5 9.5 5z"/></symbol>
    <symbol id="i-web" viewBox="0 0 12 12"><circle cx="6" cy="6" r="5"/></symbol>
  </defs>
</svg>

<section class="card card--front">
  <div class="brand"><span class="brand__name--front">HARBOR QUILL</span></div>
  <p class="tagline">Website Translation and Localisation Specialist...</p>
  <div class="contact">
    <p class="contact__name">Your Name / <span class="contact__title">Title</span></p>
    <p class="contact__row">
      <span class="contact__item"><svg class="icon"><use href="#i-phone"/></svg>123-456-7890</span>
      <span class="contact__item"><svg class="icon"><use href="#i-mobile"/></svg>123-456-7890</span>
      <span class="contact__item"><svg class="icon"><use href="#i-fax"/></svg>123-456-7890</span>
    </p>
    <p class="contact__row">
      <span class="contact__item"><svg class="icon"><use href="#i-mail"/></svg>name@website.com</span>
      <span class="contact__item"><svg class="icon"><use href="#i-web"/></svg>www.website.com</span>
    </p>
  </div>
  <div class="divider"></div>
  <p class="address">Complex name, Street name, City, State, zip code</p>
  <p class="fineprint">xxxxxxxxxxxxxxxxxxxxxxxxxxxxxxxxxxxxxxxxxxxxxxxxxx</p>
</section>

<section class="card card--back">
  <div class="brand"><span class="brand__name--back">VELMARO</span></div>
  <p class="tagline">Professional SEO Services</p>
  <div class="contact">
    <p class="contact__name">Your Name / <span class="contact__title">Title</span></p>
    <p class="contact__row">
      <span class="contact__item"><svg class="icon"><use href="#i-phone"/></svg>123-456-7890</span>
      <span class="contact__item"><svg class="icon"><use href="#i-mobile"/></svg>123-456-7890</span>
      <span class="contact__item"><svg class="icon"><use href="#i-fax"/></svg>123-456-7890</span>
    </p>
    <p class="contact__row">
      <span class="contact__item"><svg class="icon"><use href="#i-mail"/></svg>name@website.com</span>
      <span class="contact__item"><svg class="icon"><use href="#i-web"/></svg>www.website.com</span>
    </p>
  </div>
  <div class="divider"></div>
  <p class="address">Complex name, Street name, City, State, zip code</p>
  <p class="fineprint">xxxxxxxxxxxxxxxxxxxxxxxxxxxxxxxxxxxxxxxxxxxxxxxxxx</p>
</section>
</body>
</html>
```